Harborview Estates Business Card for Apartment Buildings

Create business cards for resident managers who run apartment buildings. The audience is the public who are searching for apartment rentals, and current residents who live at the apartment building. Key design element will be incorporating the company logo, however, the logo cannot dominate. The building name and manager name are more important than the logo. Current business card design leaves little room for copy, so we may need to reduce the size on the current card to allow for more space for copy.

Target Market(s)

Adults 18-65 years of age, who are looking for an apartment rental, plus current residents who live at our apartment buildings.

Industry/Entity Type

Property Management

Contact Information for Business Card

A major design element will be use of the company logo. Important property and manager contact information must be part of the design. The size of the logo will need to be reduced to make room for building and manager contact copy.

Font styles to use
Sans Serif

Colors
3176b5
000000
959595
ffffff

Requirements
Must have
• 1) Incorporate the company logo.
• 2) Use the company colors (dark blue, black/grey, over white).
• 3) FEATURE THE BUILDING NAME
• 4) FEATURE THE MANAGER NAME
• 5) The company name is less important than BUILDING and MANAGER
• 6) Manager contact information
• **SEE ATTACHED CREATIVE BRIEF**
Nice to have
• 1) Back of card logo watermark
• 2) Ability to write notes on back of carfd
Should not have
• Avoid letting the company logo dominate the card, the building name and manager are more important than the company logo.

```html
<!DOCTYPE html>
<html lang="en">
<head>
<meta charset="utf-8">
<title>Harborview Estates Business Card</title>
<link rel="stylesheet" href="https://fonts.googleapis.com/css2?family=Roboto:wght@400;500;700&family=Roboto+Condensed:wght@500;700&display=swap">
<style>
  :root {
    --brand-blue: #1a6eab;
    --card-blue: #116da9;
    --ink-grey: #4a4a4a;
    --soft-grey: #959595;
    --paper: #f4f4f4;
    --white: #ffffff;
    --backdrop: #262626;
  }
  * { margin: 0; padding: 0; box-sizing: border-box; }
  html, body { width: 1200px; height: 960px; overflow: hidden; }
  body {
    position: relative;
    background: var(--backdrop);
    font-family: "Roboto", Arial, sans-serif;
  }
  .card {
    position: absolute;
    left: 320px;
    width: 600px;
    box-shadow: 0 6px 14px rgba(0,0,0,0.45);
  }
  .card-front { top: 100px; height: 345px; background: var(--paper); }
  .card-back { top: 493px; height: 342px; background: var(--card-blue); }

  .brand-mark {
    position: absolute;
    display: flex;
    align-items: center;
    gap: 10px;
  }
  .brand-mark .brand-square {
    width: 30px; height: 30px;
    background: var(--brand-blue);
  }
  .brand-mark .brand-name {
    font-family: "Roboto Condensed", Arial, sans-serif;
    font-weight: 700;
    font-size: 26px;
    line-height: 1;
    color: var(--brand-blue);
    letter-spacing: 0.5px;
  }
  .card-front .brand-mark { left: 62px; top: 70px; }

  .property-block {
    position: absolute;
    left: 61px; top: 162px;
    color: var(--ink-grey);
    font-size: 14.5px;
    line-height: 19px;
  }
  .property-name { color: var(--brand-blue); font-weight: 700; font-size: 15px; }
  .contact-list { list-style: none; margin-top: 7px; }
  .contact-list li { display: flex; align-items: center; gap: 8px; height: 19px; }
  .contact-list svg { width: 14px; height: 14px; fill: var(--brand-blue); flex: none; }

  .manager {
    position: absolute;
    right: 33px; top: 220px;
    text-align: right;
  }
  .manager-name {
    font-family: "Roboto Condensed", Arial, sans-serif;
    font-weight: 700; font-size: 23px; color: var(--brand-blue);
    line-height: 26px;
  }
  .manager-title { font-size: 14.5px; font-weight: 500; color: var(--ink-grey); }

  .card-back .brand-mark { right: 35px; top: 232px; }
  .card-back .brand-square { background: var(--white); }
  .card-back .brand-name { color: var(--white); }
  .tagline {
    position: absolute;
    right: 35px; top: 289px;
    color: var(--white); font-weight: 700; font-size: 14.5px;
  }
</style>
</head>
<body>
  <section class="card card-front">
    <div class="brand-mark">
      <span class="brand-square"></span>
      <span class="brand-name">HARBORVIEW ESTATES</span>
    </div>

    <div class="property-block">
      <p class="property-name">Cedar Court Apartments</p>
      <p>1248 Linden Avenue</p>
      <p>Bayside, CA 90210</p>
      <ul class="contact-list">
        <li><svg viewBox="0 0 16 16"><path d="M3 1l3 .5 1 3.5-2 1.5c1 2 2.5 3.5 4.5 4.5L11 9l3.5 1 .5 3-2 2C7 15 1 9 1 3z"/></svg>555-210-4400</li>
        <li><svg viewBox="0 0 16 16"><path d="M4 0h8a1 1 0 0 1 1 1v14a1 1 0 0 1-1 1H4a1 1 0 0 1-1-1V1a1 1 0 0 1 1-1zm1 2v10h6V2z"/></svg>555-318-7720</li>
        <li><svg viewBox="0 0 16 16"><path d="M4 1h8v4H4zM1 6h14v6h-2v3H3v-3H1zm4 4v3h6v-3z"/></svg>555-642-1300</li>
        <li><svg viewBox="0 0 16 16"><path d="M1 3h14v10H1zm1.5 1.5L8 9l5.5-4.5z"/></svg>marisol@harborviewest.com</li>
        <li><svg viewBox="0 0 16 16"><circle cx="8" cy="8" r="7"/></svg>www.harborviewest.com</li>
      </ul>
    </div>

    <div class="manager">
      <p class="manager-name">Marisol Delgado</p>
      <p class="manager-title">Resident Manager</p>
    </div>
  </section>

  <section class="card card-back">
    <div class="brand-mark">
      <span class="brand-square"></span>
      <span class="brand-name">HARBORVIEW ESTATES</span>
    </div>
    <p class="tagline">Multifamily Property Management</p>
  </section>
</body>
</html>
```